Oil Field Service company needs professional business cards

Looking to clean up our current company business cards and look a little more professional. Brenwick Casing Services is a US based company that services the oil field. We deal with engineers, managers and oil rigs....................................................................................................................................................................................................................................................................................................................................................................................................

Target Market(s)

Oil and Gas professionals

Industry/Entity Type

Oil And Gas

Contact Information for Business Card

See attached photo as example

Font styles to use
Sans Serif

Colors
ec1f27

Requirements
Must have
• Company Logo, Name, Title, Cell, Office, Fax, Email.
• See attached photo
Nice to have
• External CRT, Internal CRT, Casing Crews, Torque Turn, Laydown Machine
Should not have
• Do not introduce any new pictures and keep it professional looking

```html
<!DOCTYPE html>
<html lang="en">
<head>
<meta charset="UTF-8">
<title>Brenwick Casing Services – Business Card</title>
<link rel="stylesheet" href="https://fonts.googleapis.com/css2?family=Roboto:wght@400;500;700;900&family=Roboto+Condensed:wght@400&display=swap">
<style>
  :root {
    --backdrop: #e4e4e4;
    --card: #f7f7f7;
    --navy: #3b4f61;
    --red: #ec1f27;
    --ink: #2f3438;
    --muted: #4a4f54;
    --white: #ffffff;
  }
  * { margin: 0; padding: 0; box-sizing: border-box; }
  html, body { width: 1200px; height: 576px; overflow: hidden; }
  body {
    background: var(--backdrop);
    position: relative;
    font-family: "Roboto", Arial, sans-serif;
  }
  .card {
    position: absolute;
    top: 139px;
    width: 484px;
    height: 293px;
    background: var(--card);
    border-radius: 5px;
    box-shadow: 0 2px 5px rgba(0,0,0,0.25);
    overflow: hidden;
  }
  .card--front { left: 82px; }
  .card--back { left: 602px; }

  .wordmark {
    color: var(--navy);
    font-weight: 900;
    text-transform: uppercase;
    text-align: center;
    line-height: 1.1;
  }
  .card--front .wordmark {
    position: absolute;
    left: 0; right: 0;
    top: 70px;
    font-size: 44px;
    letter-spacing: 1px;
  }
  .card--front .wordmark .wordmark__line2 { display: block; font-size: inherit; }

  .service-band {
    position: absolute;
    left: 0; right: 0;
    top: 220px;
    height: 27px;
    background: var(--red);
    color: var(--white);
    font-size: 13.5px;
    font-weight: 500;
    display: flex;
    align-items: center;
    justify-content: center;
    gap: 7px;
    white-space: nowrap;
  }
  .website-line {
    position: absolute;
    left: 0; right: 0;
    top: 262px;
    display: flex;
    align-items: center;
    justify-content: center;
    gap: 10px;
    font-size: 14px;
    color: var(--ink);
  }
  .website-line .rule { width: 82px; height: 2px; background: var(--red); }

  .holder { position: absolute; left: 23px; top: 50px; }
  .holder__name {
    font-size: 21px;
    font-weight: 900;
    color: var(--ink);
    letter-spacing: 0.2px;
  }
  .holder__title { font-size: 11.5px; color: var(--muted); margin-top: 2px; }

  .contact-list {
    position: absolute;
    left: 23px;
    top: 168px;
    list-style: none;
    font-family: "Roboto Condensed", Arial, sans-serif;
    font-size: 12px;
    color: var(--ink);
  }
  .contact-list li { display: flex; align-items: center; height: 16px; }
  .contact-list svg { width: 10px; height: 10px; margin-right: 10px; fill: var(--red); flex: none; }
  .contact-list .accent { color: var(--red); }

  .card--back .wordmark {
    position: absolute;
    left: 262px;
    width: 210px;
    top: 196px;
    font-size: 24px;
  }
</style>
</head>
<body>

<section class="card card--front">
  <div class="wordmark">Brenwick<span class="wordmark__line2">Casing Services</span></div>
  <div class="service-band">
    <span>LAYDOWN MACHINE</span><span>|</span>
    <span>CASING CREW</span><span>|</span>
    <span>MUD TOOL</span><span>|</span>
    <span>TORQUE TURN</span>
  </div>
  <div class="website-line">
    <span class="rule"></span><span>www.brenwickcs.com</span><span class="rule"></span>
  </div>
</section>

<section class="card card--back">
  <div class="holder">
    <div class="holder__name">CODY HARLAN</div>
    <div class="holder__title">Area Manager</div>
  </div>

  <ul class="contact-list">
    <li><svg viewBox="0 0 10 10" aria-hidden="true"><path d="M2 0.5 L3.6 2.8 L2.6 3.8 Q3.6 6 6.2 7.4 L7.2 6.4 L9.5 8 L8.4 9.5 Q4.5 9.5 0.5 5 Q0.3 2.5 2 0.5Z"/></svg>(555) 214-3800</li>
    <li><svg viewBox="0 0 10 10" aria-hidden="true"><path d="M0.5 3 Q5 0 9.5 3 L9.5 4 L7.5 4 L7.5 3.2 Q5 2.4 2.5 3.2 L2.5 4 L0.5 4Z M2 5 L8 5 L9 9 L1 9Z"/></svg>(555) 617-2954</li>
    <li><svg viewBox="0 0 10 10" aria-hidden="true"><path d="M2.5 0.5 H7.5 V3 H2.5Z M0.5 3.5 H9.5 V7.5 H8 V6 H2 V7.5 H0.5Z M2.5 6.5 H7.5 V9.5 H2.5Z"/></svg>(555) 214-3811</li>
    <li><svg viewBox="0 0 10 10" aria-hidden="true"><path d="M5 0.3 A3.4 3.4 0 0 1 8.4 3.7 Q8.4 6 5 9.7 Q1.6 6 1.6 3.7 A3.4 3.4 0 0 1 5 0.3Z M5 2.3 A1.4 1.4 0 1 0 5 5.1 A1.4 1.4 0 1 0 5 2.3Z" fill-rule="evenodd"/></svg>Alder Springs, OK 74020</li>
    <li><svg viewBox="0 0 10 10" aria-hidden="true"><path d="M0.5 2 H9.5 V2.6 L5 5.6 L0.5 2.6Z M0.5 3.6 L5 6.6 L9.5 3.6 V8 H0.5Z"/></svg>codyharlan@brenwickcs.com</li>
    <li><svg viewBox="0 0 10 10" aria-hidden="true"><path d="M5 0.8 A4.2 4.2 0 1 0 5 9.2 A4.2 4.2 0 1 0 5 0.8Z M1.8 4.5 H8.2 V5.5 H1.8Z M4.5 1.2 H5.5 V8.8 H4.5Z"/></svg>www.<span class="accent">brenwickcs</span>.com</li>
  </ul>

  <div class="wordmark">Brenwick Casing Services</div>
</section>

</body>
</html>
```